Print materials for 3-star hotel

We are changing up our print materials (notepads, letterheads, key card jackets, small flyer for the room rates) We are a 3 star business hotel in the Philippines and have mainly used grey tones and clean, simple lines. See attached photos for logo and hotel interior photos.

Target Market(s)

Business

Contact Information for Business Card

Corvale Terrace Hotel
Lindwell Banca Avenue corner Tolenta St Cebu City 6000 Philippines
Tel: +63 32 481 7302
Mobile: +63 917 648 2095
www.corvaleterracehotel.example

Font styles to use
Serif
Sans Serif

Requirements
Must have
• Simple
• Readable font and font size
Nice to have
• Neutral colors, grey and taupes
Should not have
• No purples and bright blues

```html
<!DOCTYPE html>
<html lang="en">
<head>
<meta charset="utf-8">
<title>Corvale Terrace Hotel — Business Card</title>
<link href="https://fonts.googleapis.com/css2?family=Cormorant+Garamond:wght@500;600&family=Open+Sans:wght@400&display=swap" rel="stylesheet">
<style>
  :root {
    --backdrop: #2b2b2c;
    --card: #121212;
    --card-edge: #1c1c1c;
    --ink: #f2f2f2;
    --ink-soft: #c9c9c9;
    --serif: "Cormorant Garamond", Georgia, serif;
    --sans: "Open Sans", Arial, sans-serif;
  }
  * { box-sizing: border-box; margin: 0; padding: 0; }
  html, body { width: 1200px; height: 1017px; overflow: hidden; background: var(--backdrop); }
  .canvas { position: relative; width: 1200px; height: 1017px; }
  .card {
    position: absolute;
    width: 560px; height: 320px;
    background: var(--card);
    border: 1px solid var(--card-edge);
    box-shadow: 0 18px 40px rgba(0,0,0,.45);
  }
  .card--front { left: 80px; top: 150px; }
  .card--back { left: 560px; top: 540px; }

  .brand-mark {
    position: absolute; left: 0; right: 0; top: 50%;
    transform: translateY(-50%);
    display: flex; align-items: center; justify-content: center; gap: 14px;
  }
  .brand-mark__square { width: 18px; height: 18px; background: var(--ink); }
  .brand-mark__name {
    font-family: var(--serif); font-weight: 600; font-size: 34px;
    letter-spacing: 5px; text-transform: uppercase; color: var(--ink);
  }

  .holder { position: absolute; right: 36px; top: 44px; text-align: right; }
  .holder__name {
    font-family: var(--serif); font-weight: 600; font-size: 22px;
    letter-spacing: 1px; text-transform: uppercase; color: var(--ink); line-height: 1.1;
  }
  .holder__title {
    font-family: var(--serif); font-weight: 500; font-size: 13px;
    letter-spacing: 1px; text-transform: uppercase; color: var(--ink-soft);
  }

  .signature {
    position: absolute; left: 36px; top: 62px;
    display: flex; flex-direction: column; align-items: flex-start; gap: 6px;
  }
  .signature__square { width: 16px; height: 16px; background: var(--ink); }
  .signature__name {
    font-family: var(--serif); font-weight: 500; font-size: 15px;
    letter-spacing: 4px; text-transform: uppercase; color: var(--ink); line-height: 1.1;
    text-align: center;
  }
  .signature__sub { display: block; font-size: 11px; letter-spacing: 5px; color: var(--ink-soft); }

  .contact { position: absolute; left: 36px; bottom: 24px; font-family: var(--sans); color: var(--ink-soft); }
  .contact__address { font-size: 11.5px; line-height: 1.45; margin-bottom: 6px; }
  .contact__list { list-style: none; }
  .contact__item { display: flex; align-items: center; gap: 9px; font-size: 11.5px; line-height: 1.6; }
  .contact__icon { width: 12px; height: 12px; flex: none; }
</style>
</head>
<body>
<main class="canvas">
  <section class="card card--front" aria-label="Business card front">
    <div class="brand-mark">
      <span class="brand-mark__square"></span>
      <span class="brand-mark__name">Corvale Terrace</span>
    </div>
  </section>

  <section class="card card--back" aria-label="Business card back">
    <div class="signature">
      <span class="signature__square"></span>
      <p class="signature__name">Corvale Terrace<span class="signature__sub">Hotel</span></p>
    </div>

    <div class="holder">
      <p class="holder__name">Rafael Almonte</p>
      <p class="holder__title">President</p>
    </div>

    <div class="contact">
      <p class="contact__address">Lindwell Banca Avenue corner Tolenta St<br>Cebu City 6000 Philippines</p>
      <ul class="contact__list">
        <li class="contact__item">
          <svg class="contact__icon" viewBox="0 0 12 12" aria-hidden="true"><path d="M2.5 1h2l1 2.5-1.3 1a6 6 0 0 0 3.3 3.3l1-1.3L11 7.5v2a1.2 1.2 0 0 1-1.3 1.2A9.5 9.5 0 0 1 1.3 2.3 1.2 1.2 0 0 1 2.5 1z" fill="#c9c9c9"/></svg>
          +63 32 481 7302
        </li>
        <li class="contact__item">
          <svg class="contact__icon" viewBox="0 0 12 12" aria-hidden="true"><rect x="3" y="0.5" width="6" height="11" rx="1" fill="none" stroke="#c9c9c9"/><circle cx="6" cy="9.5" r=".7" fill="#c9c9c9"/></svg>
          +63 917 648 2095
        </li>
        <li class="contact__item">
          <svg class="contact__icon" viewBox="0 0 12 12" aria-hidden="true"><rect x="3" y="1" width="6" height="3" fill="none" stroke="#c9c9c9"/><rect x="1" y="4" width="10" height="5" rx="1" fill="#c9c9c9"/><rect x="3" y="8" width="6" height="3" fill="#121212" stroke="#c9c9c9"/></svg>
          +63 32 481 7310
        </li>
        <li class="contact__item">
          <svg class="contact__icon" viewBox="0 0 12 12" aria-hidden="true"><rect x="0.5" y="2.5" width="11" height="7" fill="none" stroke="#c9c9c9"/><path d="M.5 2.5 6 7l5.5-4.5" fill="none" stroke="#c9c9c9"/></svg>
          r.almonte@corvaleterracehotel.example
        </li>
        <li class="contact__item">
          <svg class="contact__icon" viewBox="0 0 12 12" aria-hidden="true"><circle cx="6" cy="6" r="5.3" fill="none" stroke="#c9c9c9"/><ellipse cx="6" cy="6" rx="2.3" ry="5.3" fill="none" stroke="#c9c9c9"/><path d="M.7 6h10.6" stroke="#c9c9c9"/></svg>
          www.corvaleterracehotel.example
        </li>
      </ul>
    </div>
  </section>
</main>
</body>
</html>
```